R7M Horizon Business Card Design

We need a business card created for our New Business "R7M Horizon"<br/><br/>The business card design is up to you however the following information must be on the business card:<br/><br/>Front of the business card -<br/>Email :darrenp@r7mhorizon.nz<br/>Mobile: +64 (0) 22 4870 619<br/>Website: www.r7mhorizon.nz<br/>Card Owner Name: Darren Paltrow<br/>Company Title: Business Development Manager<br/>Slogan: "The BEST of both worlds". <br/>Logo On the front attached to the design brief<br/><br/>On the back: <br/>Space on the back for 4 more versions of the logo across the bottom of the card indicating different subsidiary brands - R7M Coffee, R7M Arts, R7M ?? (The card will be used for all of these brands - We Will add the extra subsidiary logos to the design once the design is finished (We are a graphics design team). <br/><br/>Other than that we want a premium feeling logo that remains universally usable depending on the business entity that we are using the card for. The use of bright bold colours would be great but we still want the card to feel premium.
Target Market(s)
Gift Design and Manufacturing Companies
Contact Information for Business Card
Front of the business card -
Email :darrenp@r7mhorizon.nz
Mobile: +64 (0) 22 4870 619
Website: www.r7mhorizon.nz
Card Owner Name: Darren Paltrow
Company Title: Business Development Manager
Slogan: "The BEST of both worlds".
Logo On the front attached to the design brief

```html
<!DOCTYPE html>
<html lang="en">
<head>
<meta charset="utf-8">
<title>R7M Horizon – Business Card</title>
<link rel="stylesheet" href="https://fonts.googleapis.com/css2?family=Montserrat:wght@700&family=Arimo:wght@400&display=swap">
<style>
  :root {
    --brand-blue: #34449c;
    --card-white: #ffffff;
    --arc-black: #1c1c1c;
    --backdrop: #e9eaee;
    --text-light: #ffffff;
    --divider: rgba(255, 255, 255, 0.3);
  }
  html, body {
    margin: 0;
    width: 1200px;
    height: 900px;
    overflow: hidden;
    background: var(--backdrop);
  }
  .stage {
    width: 1200px;
    height: 900px;
    display: flex;
    align-items: center;
    justify-content: center;
  }
  .business-card {
    width: 920px;
    height: 569px;
    display: block;
    background: var(--card-white);
    box-shadow: 0 18px 40px rgba(20, 25, 60, 0.18);
  }
  .card-panel { fill: var(--brand-blue); }
  .card-arc { fill: none; stroke: var(--arc-black); stroke-width: 4; }
  .holder-name {
    font-family: "Montserrat", sans-serif;
    font-weight: 700;
    font-size: 20px;
    letter-spacing: 0.4px;
    fill: var(--text-light);
  }
  .holder-title, .contact-line {
    font-family: "Arimo", Arial, sans-serif;
    font-size: 17px;
    fill: var(--text-light);
  }
  .contact-icon { fill: none; stroke: var(--text-light); stroke-width: 1.4; }
  .panel-divider { stroke: var(--divider); stroke-width: 1; }
  .slogan {
    font-family: "Montserrat", sans-serif;
    font-weight: 700;
    font-size: 23px;
    fill: var(--text-light);
  }
  .brand-name {
    font-family: "Montserrat", sans-serif;
    font-weight: 700;
    font-size: 32px;
    fill: var(--brand-blue);
  }
</style>
</head>
<body>
<main class="stage">
  <svg class="business-card" viewBox="0 0 655 405" role="group" aria-label="R7M Horizon business card for Darren Paltrow">
    <path class="card-arc" d="M226,0 C311,40 371,130 363,210 C356,300 301,375 247,405"/>
    <path class="card-panel" d="M0,0 H215 C300,40 360,130 352,210 C345,300 290,375 237,405 H0 Z"/>

    <text class="holder-name" x="30" y="101">DARREN PALTROW</text>
    <text class="holder-title" x="30" y="125">Business Development Manager</text>

    <g class="contact-phone">
      <rect class="contact-icon" x="30" y="145" width="16" height="16" rx="2"/>
      <path class="contact-icon" d="M34,148 c0,6 4,10 9,10 l1,-2 -3,-2 -1,1 c-2,-1 -3,-2 -4,-4 l1,-1 -2,-3 z"/>
      <text class="contact-line" x="53" y="160">+64 (0) 22 4870 619</text>
    </g>
    <g class="contact-email">
      <rect class="contact-icon" x="30" y="172" width="17" height="12"/>
      <path class="contact-icon" d="M30,172 L38.5,179 L47,172"/>
      <text class="contact-line" x="53" y="184">darrenp@r7mhorizon.nz</text>
    </g>
    <g class="contact-web">
      <circle class="contact-icon" cx="38.5" cy="202" r="8"/>
      <ellipse class="contact-icon" cx="38.5" cy="202" rx="3.5" ry="8"/>
      <path class="contact-icon" d="M30.5,202 H46.5 M32,197.5 H45 M32,206.5 H45"/>
      <text class="contact-line" x="53" y="208">www.r7mhorizon.nz</text>
    </g>

    <line class="panel-divider" x1="30" y1="246" x2="287" y2="246"/>

    <text class="slogan" x="30" y="287">THE BEST OF</text>
    <text class="slogan" x="30" y="318">BOTH WORLDS</text>

    <text class="brand-name" x="510" y="285" text-anchor="middle">R7M Horizon</text>
  </svg>
</main>
</body>
</html>
```